Coastal Learner Bureau business cards

Australian company about to start offering its services. We recruit international students to come to study English, vocational education and postgraduate courses in Australia. We help them find the institution and select the right city they want to come to Australia. We are a young, online oriented and supportive agency. Our clients are between 18 and 35 years old, mainly University students, young professionals or people with work experience. We provide much more information that any other agency offer. We administrate a Facebook group with more than 11.000 members that daily ask questions about general information when coming to Australia, while they are here and even after they leave the country

Target Market(s)

International students from South America, Central America and Europe

Industry/Entity Type

Student

Contact Information for Business Card

Tomas Bilbrea
Managing Director
tomas@kelvarin.com.au
www.kelvoria.com.au
+61 491058264
Melbourne, Australia

Font styles to use
Serif
Sans Serif

Colors

Designer to choose colors to be used in the design.

Requirements
Must have
• Horizontal design
• Standard business card size and shape. If font uses green or yellow colours, they will have to match the ones from the logo
Nice to have
• UPDATE: Use the contents of the green image to design one of the card sides. Use our logo in the background of that side as watermark.
• Passport image, or immigration stamps. A picture of the Yarra River (from Melbourne) would be cool as well.
Should not have
• Non-standard business card size and shape
• Not black as the background colour of any sides as we are not a VIP agency or a hight class service. We are orientes to young people and they like colours, pictures, something attractive.
• Vertical design
• NO YELLOW or BLACK AS THE BACKGROUND COLOUR OF ANY SIDE OF THE BIZ CARD

```html
<!DOCTYPE html>
<html lang="en">
<head>
<meta charset="utf-8">
<title>Coastal Learner Bureau – Business Cards</title>
<link href="https://fonts.googleapis.com/css2?family=Open+Sans:wght@400;600;700&display=swap" rel="stylesheet">
<style>
  :root {
    --page-bg: #e9e9e6;
    --gold-light: #f0d21a;
    --gold: #dcb010;
    --green-light: #1c7a47;
    --green: #146239;
    --green-dark: #0e4d2c;
    --paper: #f4f4f2;
    --white: #ffffff;
  }
  * { box-sizing: border-box; margin: 0; padding: 0; }
  html, body {
    width: 1200px; height: 900px; overflow: hidden;
    background: var(--page-bg);
    font-family: "Open Sans", Arial, sans-serif;
  }
  .card {
    position: absolute; left: 250px;
    width: 700px; height: 400px;
    overflow: hidden;
    box-shadow: 0 6px 18px rgba(0,0,0,0.18);
  }
  /* Front side */
  .card-front {
    top: 30px;
    background: linear-gradient(100deg, var(--green-light) 0%, var(--green) 55%, var(--green-dark) 100%);
  }
  .front-brand {
    position: absolute; left: 0; right: 0; top: 130px;
    display: flex; justify-content: center; align-items: center; gap: 14px;
  }
  .front-brand .brand-name {
    font-size: 64px; font-weight: 700; color: var(--white); letter-spacing: 1px;
  }
  .brand-dot {
    width: 18px; height: 18px; border-radius: 50%; background: var(--gold);
  }
  .tagline {
    position: absolute; left: 0; right: 0; top: 296px;
    display: flex; justify-content: center; align-items: center; gap: 12px;
    color: var(--white); font-size: 15px; font-weight: 600;
  }
  .tagline .rule { width: 190px; height: 1px; background: var(--gold); }

  /* Back side */
  .card-back { top: 470px; background: var(--paper); }
  .back-shape { position: absolute; inset: 0; }
  .back-brand {
    position: absolute; left: 70px; top: 150px;
    display: flex; align-items: center; gap: 12px;
  }
  .back-brand .brand-name {
    font-size: 58px; font-weight: 700; color: var(--green);
  }
  .contact {
    position: absolute; right: 32px; top: 104px;
    text-align: right; color: var(--white);
  }
  .contact-name { color: var(--gold-light); font-weight: 700; font-size: 19px; letter-spacing: 0.5px; }
  .contact-role { font-size: 17px; letter-spacing: 0.5px; margin-bottom: 16px; }
  .contact-line {
    display: flex; justify-content: flex-end; align-items: center; gap: 8px;
    font-size: 15px; line-height: 25px;
  }
  .contact-line svg { width: 14px; height: 14px; flex: none; }
</style>
</head>
<body>

<section class="card card-front" aria-label="Card front">
  <div class="front-brand">
    <span class="brand-name">Kelvoria</span>
    <span class="brand-dot"></span>
  </div>
  <div class="tagline">
    <span class="rule"></span>
    <span>Hacemos más por ti!</span>
    <span class="rule"></span>
  </div>
</section>

<section class="card card-back" aria-label="Card back">
  <svg class="back-shape" viewBox="0 0 700 400" width="700" height="400" aria-hidden="true">
    <path d="M505 0 C430 130 470 300 290 400 L700 400 L700 0 Z" fill="var(--gold)"/>
    <path d="M520 0 C450 130 490 300 310 400 L700 400 L700 0 Z" fill="var(--green)"/>
  </svg>

  <div class="back-brand">
    <span class="brand-name">Kelvoria</span>
    <span class="brand-dot"></span>
  </div>

  <div class="contact">
    <p class="contact-name">TOMAS BILBREA</p>
    <p class="contact-role">MANAGING DIRECTOR</p>
    <p class="contact-line">Melbourne, Australia
      <svg viewBox="0 0 14 14"><path d="M7 1a4 4 0 0 0-4 4c0 3 4 8 4 8s4-5 4-8a4 4 0 0 0-4-4z" fill="var(--gold-light)"/><circle cx="7" cy="5" r="1.5" fill="var(--green)"/></svg>
    </p>
    <p class="contact-line">+61 491058264
      <svg viewBox="0 0 14 14"><path d="M3 1h3l1 3-2 1.5a8 8 0 0 0 3.5 3.5L10 7l3 1v3a2 2 0 0 1-2 2A10 10 0 0 1 1 3a2 2 0 0 1 2-2z" fill="var(--gold-light)"/></svg>
    </p>
    <p class="contact-line">tomas@kelvarin.com.au
      <svg viewBox="0 0 14 14"><rect x="1" y="3" width="12" height="8" fill="var(--gold-light)"/><path d="M1 3l6 5 6-5" stroke="var(--green)" fill="none"/></svg>
    </p>
    <p class="contact-line">www.kelvoria.com.au
      <svg viewBox="0 0 14 14"><circle cx="7" cy="7" r="6" fill="var(--gold-light)"/><path d="M1 7h12M7 1c-3 3-3 9 0 12M7 1c3 3 3 9 0 12" stroke="var(--green)" fill="none"/></svg>
    </p>
  </div>
</section>

</body>
</html>
```